Varnik Holdings — Business Card Design Brief
Overview
Design a double-sided business card for Varnik Holdings that highlights our two service arms: Varnik Communications (telecommunications) and Varnik Energy (business energy solutions). The card should feel smart and stand out when handed to clients.

Objectives
Showcase our areas of specialty clearly.
Reflect the overall Varnik / Varnik Holdings brand while acknowledging both arms.
Explore using both logos (Communications + Energy) or one unified logo, depending on the design.

Deliverables
One double-sided business card design (front + back).

Content & Copy
Front (preferred): Logo: Varnik / Varnik Holdings
Descriptor: Business Communications | Business Energy
Back:My contact details and company details
Core products: Business Mobile • Telephony • Internet • Business Energy Solutions

Brand & Visual Direction
We have a group logo currently tailored more toward telecoms, plus a separate Varnik Energy logo.
Please explore layouts that use both logos or just one, whichever works best.
Color: I wouldn't mind seeing an option using our the Blue/Purple gradient from our website (varnik-example.co.uk), but also open to non-gradient approaches and other colours..

Overall look: Smart, modern, and distinctive.
Format & Print Specs
Double-sided business card format. (Use a standard size

Must-Haves
Front: Varnik wording or Varnik Holdings wording with atleast 1 logo also on front “Business Communications | Business Energy.”

Back: Contact + company details and core products.
A design that stands out while remaining professional.

Nice-to-Have Options
A gradient version using our site’s Blue/Purple gradient.
A non-gradient version.
A dual-logo treatment versus a single-logo treatment.

Thanks
Owen

```html
<!DOCTYPE html>
<html lang="en">
<head>
<meta charset="utf-8">
<title>Varnik Holdings — Business Card</title>
<link rel="stylesheet" href="https://fonts.googleapis.com/css2?family=Arimo:wght@400;700&display=swap">
<style>
  :root {
    --navy: #1c1b6e;
    --green: #3fae1d;
    --lime: #d8d800;
    --leaf: #22a30f;
    --ink: #3a3a3a;
    --bg: #e9e9e9;
    --white: #ffffff;
    --yellow-name: #e9f20a;
    --green-name: #1f6d10;
  }
  * { margin: 0; padding: 0; box-sizing: border-box; }
  html, body { width: 1200px; height: 1200px; overflow: hidden; }
  body {
    background: var(--bg);
    font-family: "Arimo", Arial, sans-serif;
    position: relative;
  }
  .card {
    position: absolute;
    left: 265px;
    width: 690px;
    height: 394px;
    overflow: hidden;
  }
  .card--front { top: 159px; background: var(--white); }
  .card--back {
    top: 653px;
    background: linear-gradient(180deg, var(--lime) 0%, #9ccb08 50%, var(--leaf) 100%);
  }

  /* front */
  .brand {
    position: absolute;
    left: 80px; top: 140px;
    width: 270px;
    display: flex; align-items: center; gap: 14px;
  }
  .brand__dot {
    width: 34px; height: 34px; border-radius: 50%;
    background: var(--green); flex: none;
  }
  .brand__name {
    font-weight: 700; font-size: 56px; color: var(--navy);
    letter-spacing: 1px; line-height: 1;
  }
  .divider {
    position: absolute; width: 2px; background: #d7d7d7;
  }
  .card--front .divider { left: 367px; top: 60px; height: 232px; }
  .contact {
    position: absolute; left: 398px; top: 74px;
    color: var(--ink);
  }
  .contact__name {
    font-weight: 700; font-size: 27px; color: var(--navy); letter-spacing: .5px;
  }
  .contact__role { font-size: 16px; color: var(--green); margin-top: 2px; }
  .contact__address { font-size: 17px; line-height: 21px; margin-top: 20px; }
  .contact__list { list-style: none; margin-top: 13px; font-size: 17px; line-height: 20.5px; }
  .contact__list li { display: flex; align-items: center; gap: 10px; }
  .contact__list svg { width: 14px; height: 14px; fill: var(--navy); flex: none; }

  .products {
    position: absolute; left: 0; top: 324px; width: 100%; height: 35px;
    display: flex;
  }
  .products__band {
    width: 536px; background: var(--navy); color: var(--white);
    font-size: 16px; display: flex; align-items: center; padding-left: 29px;
    white-space: nowrap;
  }
  .products__mark {
    width: 44px; background: var(--white);
    display: flex; align-items: center; justify-content: center;
  }
  .products__mark span {
    width: 18px; height: 18px; border-radius: 50%; background: var(--green);
  }
  .products__fade {
    flex: 1;
    background: linear-gradient(90deg, #c7e200 0%, #e6ee00 45%, var(--leaf) 100%);
  }

  /* back */
  .card--back .divider { left: 354px; top: 101px; height: 201px; background: rgba(255,255,255,.75); }
  .arm {
    position: absolute; top: 96px; width: 320px;
    display: flex; flex-direction: column; align-items: center;
  }
  .arm--comms { left: 40px; }
  .arm--energy { left: 342px; }
  .arm__dot { width: 64px; height: 64px; border-radius: 50%; margin-bottom: 26px; }
  .arm--comms .arm__dot { background: rgba(31,109,16,.55); }
  .arm--energy .arm__dot { background: var(--yellow-name); }
  .arm__name { font-weight: 700; font-size: 56px; line-height: 1; letter-spacing: 1px; }
  .arm--comms .arm__name { color: var(--green-name); }
  .arm--energy .arm__name { color: var(--yellow-name); }
  .arm__label { color: var(--white); font-size: 16px; margin-top: 20px; }
  .arm--energy .arm__label { letter-spacing: 3.5px; }
</style>
</head>
<body>

<section class="card card--front" aria-label="Business card, contact side">
  <div class="brand">
    <span class="brand__dot"></span>
    <span class="brand__name">VARNIK</span>
  </div>
  <div class="divider"></div>
  <div class="contact">
    <p class="contact__name">DANIEL MARSH</p>
    <p class="contact__role">President</p>
    <p class="contact__address">412 Alder Court<br>Kelwood, Canada 58210</p>
    <ul class="contact__list">
      <li><svg viewBox="0 0 16 16"><path d="M3.6 1l2.6 3-1.5 2a9 9 0 0 0 4.7 4.7l2-1.5 3 2.6-1.4 2.4C7.3 14.5 1.5 8.7 1.2 2.4z"/></svg>555-201-4870</li>
      <li><svg viewBox="0 0 16 16"><path d="M4 0h8v16H4zM5.5 2v10h5V2zM7 13.2h2v1.4H7z" fill-rule="evenodd"/></svg>555-203-9162</li>
      <li><svg viewBox="0 0 16 16"><path d="M1 3h14v10H1zM2.5 4.5L8 8.5l5.5-4z"/></svg>info@varnik-example.com</li>
      <li><svg viewBox="0 0 16 16"><circle cx="8" cy="8" r="7"/></svg>www.varnik-example.com</li>
    </ul>
  </div>
  <div class="products">
    <div class="products__band">Business Mobile &nbsp;•&nbsp; Telephony &nbsp;•&nbsp; Internet &nbsp;•&nbsp; Business Energy Solutions</div>
    <div class="products__mark"><span></span></div>
    <div class="products__fade"></div>
  </div>
</section>

<section class="card card--back" aria-label="Business card, brand side">
  <div class="arm arm--comms">
    <span class="arm__dot"></span>
    <span class="arm__name">VARNIK</span>
    <span class="arm__label">BUSINESS COMMUNICATIONS</span>
  </div>
  <div class="divider"></div>
  <div class="arm arm--energy">
    <span class="arm__dot"></span>
    <span class="arm__name">VARNIK</span>
    <span class="arm__label">BUSINESS ENERGY</span>
  </div>
</section>

</body>
</html>
```